Website for new child psychology practice

New clinical psychology practice in NSW Australia, specialising in work with children, adolescents and families. I would like to feature the colours in the logo, which was recently designed by pixelharbor designer Odette.
I am seeking a professional looking page, which is easy to navigate and is colourful and playful but not childish.
Target Market(s)
Parents and professionals
Industry/Entity Type
Health
Coding
Coded - Design and coding required
Number of Pages Required
1 page
Font styles to use
Serif
Requirements
Must have
- Pages for 'About us' 'Services' 'Fees and information' 'Contact us'
Should not have
- Childish stock photos

```html
<!DOCTYPE html>
<html lang="en">
<head>
<meta charset="utf-8">
<title>Dr Clara Hayes – Clinical Psychologist</title>
<link rel="stylesheet" href="https://fonts.googleapis.com/css2?family=Tinos:wght@400;700&family=Roboto:wght@300;400;500;700&display=swap">
<style>
:root{
  --purple:#a3308f;
  --purple-dark:#8a2479;
  --orange:#e8871e;
  --pink-soft:#f2dcef;
  --blush:#fbf6f6;
  --navy:#1e2236;
  --navy-bar:#2c3048;
  --ink:#1f2a44;
  --muted:#6d6f7a;
  --line:#e4e4ea;
  --white:#fff;
}
*{box-sizing:border-box;margin:0;padding:0}
html,body{width:1200px;height:5271px;overflow:hidden}
body{position:relative;background:var(--white);font-family:"Roboto",sans-serif;color:var(--muted)}
.abs{position:absolute}
.serif{font-family:"Tinos",serif;color:var(--ink);font-weight:400}
.photo{position:absolute}
.btn{position:absolute;display:flex;align-items:center;justify-content:center;font-size:12px;font-weight:500;border-radius:3px}
.btn-orange{background:var(--orange);color:#fff}
.btn-outline{border:1.5px solid #555;color:#222;background:#fff}
p.small{font-size:11px;line-height:17px;color:var(--muted)}

/* header */
.site-header{position:absolute;left:0;top:0;width:1200px;height:78px;background:var(--pink-soft)}
.brand{position:absolute;display:flex;align-items:center;gap:8px}
.brand-dot{width:34px;height:34px;border-radius:50%;background:var(--purple)}
.brand-name{font-family:"Tinos",serif;font-size:21px;color:var(--ink);letter-spacing:.5px;line-height:1}
.brand-name small{display:block;font-size:8px;letter-spacing:2px;color:var(--purple)}
.main-nav{position:absolute;left:368px;top:30px;display:flex;gap:36px;font-size:10px;font-weight:500;color:#333;letter-spacing:.4px}
.support{position:absolute;left:900px;top:16px;display:flex;gap:12px;align-items:center}
.support .label{font-family:"Tinos",serif;font-size:12px;color:#444}
.support .num{font-size:14px;font-weight:700;color:var(--ink)}

/* hero */
.hero-card{position:absolute;left:0;top:195px;width:516px;height:495px;background:#fff;box-shadow:0 6px 30px rgba(0,0,0,.08)}
.hero-card .bar{position:absolute;left:62px;top:126px;width:4px;height:278px;background:var(--purple)}
.hero-card h1{position:absolute;left:133px;top:130px;font-size:50px;line-height:53px;width:360px}
.hero-card p{position:absolute;left:133px;top:298px;width:335px}
.badge{position:absolute;left:461px;top:197px;width:108px;height:94px;background:var(--purple);color:#fff;text-align:center;padding-top:16px;font-size:9px;line-height:12px}
.badge b{display:block;font-family:"Tinos",serif;font-weight:400;font-size:30px;line-height:34px}
.social-rail{position:absolute;left:1145px;top:92px;display:flex;flex-direction:column;gap:12px}
.social-rail span{width:22px;height:22px;border-radius:50%;background:#fff;border:1.5px solid var(--purple)}

/* why */
.feature{position:absolute;width:192px;background:#fff;box-shadow:0 4px 16px rgba(0,0,0,.1);border-top:3px solid var(--ink);padding:34px 26px 0}
.feature.active{background:var(--purple);border-top:none}
.feature .ico{width:42px;height:42px;background:#f1eaf4;border-radius:3px;display:flex;align-items:center;justify-content:center;margin-bottom:14px}
.feature.active .ico{background:rgba(255,255,255,.25)}
.feature h4{font-family:"Tinos",serif;font-weight:400;font-size:17px;color:var(--ink);padding-bottom:4px;border-bottom:1px solid var(--purple);display:inline-block;margin-bottom:14px}
.feature.active h4,.feature.active p{color:#fff;border-color:#fff}
.feature p{font-size:10px;line-height:16px}
.why-text{position:absolute;right:236px;top:895px;width:300px;text-align:right}
.why-text h2{font-size:46px;line-height:56px}
.why-text h3{font-weight:400;font-size:20px;line-height:29px;color:#333;margin-top:20px}
.why-text p{margin-top:10px;font-size:10px;line-height:16px}

/* services */
.services{position:absolute;left:0;top:1337px;width:1200px;height:615px;background:var(--blush)}
.sec-title{position:absolute;width:100%;text-align:center;font-size:46px}
.sec-title::after{content:"";display:block;width:80px;height:2px;background:var(--purple);margin:8px auto 0}
.svc{position:absolute;top:183px;width:326px;height:345px;background:#fff;border-bottom:3px solid var(--orange);text-align:center}
.svc .photo{left:0;top:0;width:326px;height:196px}
.svc .icon{position:absolute;left:133px;top:166px;width:60px;height:60px;border-radius:50%;background:var(--purple);border:6px solid #e7c4df;display:flex;align-items:center;justify-content:center}
.svc h4{position:absolute;top:248px;width:100%;font-size:21px;font-weight:400;color:#333}
.svc p{position:absolute;top:282px;left:18px;right:18px;font-size:10px;line-height:16px}

/* video */
.video-frame{position:absolute;left:235px;top:1952px;width:965px;height:682px;background:var(--purple);border-radius:10px 0 0 0}
.video{position:absolute;left:0;top:2021px;width:1067px;height:537px;border-radius:0 10px 10px 0;overflow:hidden}
.video h2{position:absolute;top:285px;width:100%;text-align:center;color:#fff;font-size:44px;line-height:56px}
.play{position:absolute;left:546px;top:137px;width:104px;height:104px;border-radius:50%;background:rgba(255,255,255,.25);display:flex;align-items:center;justify-content:center}
.play span{width:58px;height:58px;border-radius:50%;background:#fff;display:flex;align-items:center;justify-content:center}
.follow{position:absolute;left:1128px;top:2160px;color:#fff;font-size:11px;writing-mode:vertical-rl}
.follow-line{position:absolute;left:1138px;top:2240px;width:1px;height:160px;background:rgba(255,255,255,.7)}
.follow-icons{position:absolute;left:1128px;top:2412px;display:flex;flex-direction:column;gap:14px}
.follow-icons span{width:22px;height:22px;border-radius:50%;border:1.5px solid #fff}

/* projects */
.projects-title{position:absolute;right:235px;top:2688px;font-size:46px}
.projects-sub{position:absolute;right:235px;top:2782px;font-size:18px;color:#555}
.proj-card{position:absolute;left:233px;top:3066px;width:334px;height:133px;background:#fff;box-shadow:0 4px 18px rgba(0,0,0,.1);padding:24px 20px}
.proj-card h4{font-family:"Tinos",serif;font-weight:400;font-size:20px;color:var(--purple);padding-bottom:4px;border-bottom:1px solid var(--purple);display:inline-block;margin-bottom:14px}
.arrow-btn{position:absolute;left:184px;width:32px;height:32px;background:var(--orange);border-radius:3px;display:flex;align-items:center;justify-content:center}

/* reasons */
.reasons-card{position:absolute;left:176px;top:3441px;width:370px;height:450px;background:#fff;box-shadow:0 6px 24px rgba(0,0,0,.12);padding:38px 30px}
.reasons-card h2{font-size:32px;line-height:38px;padding:0 0 14px 0;margin:0 -30px 0 -30px;padding-left:30px;border-bottom:2px solid var(--purple)}
.reasons-card p{margin-top:16px;font-size:10px;line-height:16px}
.ticks{list-style:none;margin-top:18px}
.ticks li{display:flex;align-items:center;gap:10px;font-size:10px;line-height:21px}
.ticks li i{width:10px;height:10px;border:1.5px solid var(--purple);display:inline-block}

/* contact */
.contact-title{position:absolute;left:139px;top:4130px;font-size:40px;line-height:46px}
.contact-intro{position:absolute;left:139px;top:4250px;width:360px;font-size:13px;line-height:22px}
.contact-rule{position:absolute;left:139px;top:4350px;width:380px;height:1px;background:var(--line)}
.contact-item{position:absolute;left:139px;display:flex;align-items:center;gap:22px;font-size:13px;color:#555}
.contact-item .ci{width:24px;height:24px;border-radius:50%;background:#f3e6f1;display:flex;align-items:center;justify-content:center}
.form-card{position:absolute;left:592px;top:4080px;width:487px;height:544px;background:#fff;border-top:3px solid var(--purple);box-shadow:0 4px 24px rgba(0,0,0,.1)}
.form-card label{position:absolute;font-size:13px;font-weight:700;color:#222}
.form-card .field{position:absolute;border:1px solid #ddd;font-size:11px;color:#999;padding:14px 16px}

/* footer */
.footer{position:absolute;left:0;top:4694px;width:1200px;height:528px;background:var(--navy);color:#fff}
.footer h5{position:absolute;font-size:20px;font-weight:500}
.foot-links{position:absolute;list-style:none;font-size:13px;line-height:31px}
.foot-links li::before{content:"›";margin-right:12px}
.sub{position:absolute;left:786px;top:246px;width:322px;height:48px;background:var(--navy-bar);border-radius:24px;font-size:12px;font-weight:500;padding:16px 26px}
.sub span{position:absolute;right:0;top:0;width:54px;height:48px;border-radius:24px;background:var(--purple);display:flex;align-items:center;justify-content:center}
.info-bar{position:absolute;left:86px;top:432px;width:1026px;height:86px;background:var(--navy-bar);border-radius:6px}
.info{position:absolute;top:24px;display:flex;gap:18px;font-size:15px;line-height:20px}
.info b{font-weight:700}
.legal{position:absolute;top:5236px;font-size:12px;color:#444}
.to-top{position:absolute;left:1126px;top:5181px;width:47px;height:47px;background:var(--orange);border-radius:4px;display:flex;align-items:center;justify-content:center}
</style>
</head>
<body>

<!-- header -->
<header class="site-header">
  <div class="brand" style="left:84px;top:20px"><span class="brand-dot"></span><span class="brand-name">DR CLARA HAYES<small>CLINICAL PSYCHOLOGIST</small></span></div>
  <nav class="main-nav"><span>HOME</span><span>ABOUT US</span><span>SERVICES</span><span>BLOGS</span><span>PRICING</span><span>CONTACT US</span></nav>
  <div class="support">
    <svg width="26" height="26" viewBox="0 0 24 24"><path d="M6.6 10.8a15 15 0 0 0 6.6 6.6l2.2-2.2c.3-.3.7-.4 1-.2 1.1.4 2.3.6 3.6.6.6 0 1 .4 1 1V20c0 .6-.4 1-1 1A17 17 0 0 1 3 4c0-.6.4-1 1-1h3.5c.6 0 1 .4 1 1 0 1.3.2 2.5.6 3.6.1.3 0 .7-.2 1z" fill="#e8871e"/></svg>
    <div><div class="label">Get Support</div><div class="num">+61 400 218 650</div></div>
  </div>
</header>

<!-- hero -->
<div class="photo" role="img" aria-label="Therapist taking notes while a client rests on a leather couch" style="left:133px;top:78px;width:1067px;height:608px;background:linear-gradient(120deg,#ece7e3 0%,#b7aaa0 45%,#4b3e36 75%,#2e2622 100%)"></div>
<section class="hero-card">
  <span class="bar"></span>
  <h1 class="serif">Empowering You on Your Healing Journey</h1>
  <p class="small">Lorem ipsum dolor sit amet, consectetur adipiscing elit, sed do eius mod tempor incididunt ut labore et dolore magna aliqua. Ut enim ad minim veniam, quis nostrud</p>
  <div class="btn btn-orange" style="left:133px;top:364px;width:120px;height:42px">Learn More</div>
  <div class="btn btn-outline" style="left:273px;top:364px;width:120px;height:42px">Our Services</div>
</section>
<div class="badge"><b>20+</b>Years of<br>Experience</div>
<div class="social-rail"><span></span><span></span><span></span><span></span></div>

<!-- why choose us -->
<div class="feature" style="left:235px;top:764px;height:213px">
  <div class="ico"><svg width="18" height="18" viewBox="0 0 20 20"><circle cx="10" cy="7" r="4" fill="none" stroke="#a3308f" stroke-width="1.5"/><path d="M3 18c1-4 13-4 14 0" fill="none" stroke="#a3308f" stroke-width="1.5"/></svg></div>
  <h4>Professionalism</h4><p>Lorem ipsum dolor sit amet, consectetur adipiscing elit, sed do</p>
</div>
<div class="feature" style="left:235px;top:993px;height:215px">
  <div class="ico"><svg width="18" height="18" viewBox="0 0 20 20"><circle cx="6" cy="7" r="3" fill="none" stroke="#a3308f" stroke-width="1.5"/><circle cx="14" cy="7" r="3" fill="none" stroke="#a3308f" stroke-width="1.5"/><path d="M1 17c1-4 9-4 10 0M9 17c1-4 9-4 10 0" fill="none" stroke="#a3308f" stroke-width="1.5"/></svg></div>
  <h4>Client-centric</h4><p>Lorem ipsum dolor sit amet, consectetur adipiscing elit, sed do</p>
</div>
<div class="feature active" style="left:453px;top:821px;height:211px">
  <div class="ico"><svg width="18" height="18" viewBox="0 0 20 20"><path d="M3 13a7 7 0 0 1 14 0" fill="none" stroke="#fff" stroke-width="1.5"/><rect x="2" y="12" width="3" height="5" fill="#fff"/><rect x="15" y="12" width="3" height="5" fill="#fff"/></svg></div>
  <h4>Empathetic Staff</h4><p>Lorem ipsum dolor sit amet, consectetur adipiscing elit, sed do</p>
</div>
<div class="feature" style="left:453px;top:1050px;height:216px">
  <div class="ico"><svg width="18" height="18" viewBox="0 0 20 20"><path d="M10 2l2.4 5 5.6.6-4.2 3.8 1.2 5.6L10 14l-5 3 1.2-5.6L2 7.6 7.6 7z" fill="none" stroke="#a3308f" stroke-width="1.5"/></svg></div>
  <h4>Calm Environment</h4><p>Lorem ipsum dolor sit amet, consectetur adipiscing elit, sed do</p>
</div>
<div class="why-text">
  <h2 class="serif">Why Choose Us</h2>
  <h3>Transform Your Life,<br>Embrace Your Authentic Self</h3>
  <p>Lorem ipsum dolor sit amet, consectetur adipiscing elit, se d do eiusmod tempor incididunt ut labore et dolore magn a aliqua. Ut enim ad minim veniam, quis nostrud exercitation ullamco laboris nisi</p>
</div>
<div class="btn btn-orange" style="left:843px;top:1165px;width:122px;height:42px">View All</div>

<!-- services -->
<section class="services">
  <h2 class="sec-title serif" style="top:66px">Our Services</h2>
  <article class="svc" style="left:86px">
    <div class="photo" role="img" aria-label="Counsellor talking with a young client" style="background:linear-gradient(135deg,#d9d4cf,#a89b90)"></div>
    <div class="icon"><svg width="24" height="24" viewBox="0 0 20 20"><path d="M3 13a7 7 0 0 1 14 0" fill="none" stroke="#fff" stroke-width="1.6"/><rect x="2" y="12" width="3" height="5" fill="#fff"/><rect x="15" y="12" width="3" height="5" fill="#fff"/></svg></div>
    <h4>Behavioral Intervention</h4><p>Lorem ipsum dolor sit amet, consectetur adipiscing elit, se d do eiusmod tempor incididunt ut labore</p>
  </article>
  <article class="svc" style="left:436px">
    <div class="photo" role="img" aria-label="Therapist writing on a clipboard during a family session" style="background:linear-gradient(135deg,#e4e1dc,#9d9690)"></div>
    <div class="icon"><svg width="24" height="24" viewBox="0 0 20 20"><path d="M3 13a7 7 0 0 1 14 0" fill="none" stroke="#fff" stroke-width="1.6"/><rect x="2" y="12" width="3" height="5" fill="#fff"/><rect x="15" y="12" width="3" height="5" fill="#fff"/></svg></div>
    <h4>Family Therapy</h4><p>Lorem ipsum dolor sit amet, consectetur adipiscing elit, se d do eiusmod tempor incididunt ut labore</p>
  </article>
  <article class="svc" style="left:788px">
    <div class="photo" role="img" aria-label="Client relaxing on a couch while a psychologist listens" style="background:linear-gradient(135deg,#cfc7bf,#6d5f56)"></div>
    <div class="icon"><svg width="24" height="24" viewBox="0 0 20 20"><path d="M3 13a7 7 0 0 1 14 0" fill="none" stroke="#fff" stroke-width="1.6"/><rect x="2" y="12" width="3" height="5" fill="#fff"/><rect x="15" y="12" width="3" height="5" fill="#fff"/></svg></div>
    <h4>Stress Management</h4><p>Lorem ipsum dolor sit amet, consectetur adipiscing elit, se d do eiusmod tempor incididunt ut labore</p>
  </article>
</section>

<!-- video -->
<div class="video-frame"></div>
<section class="video" role="img" aria-label="Hands clasped together in a dim, calm therapy room" style="background:linear-gradient(120deg,#4c4a48,#2d2b2a 60%,#3d3b39)">
  <div class="play"><span><svg width="18" height="18" viewBox="0 0 20 20"><path d="M6 3l11 7-11 7z" fill="#a3308f"/></svg></span></div>
  <h2 class="serif" style="color:#fff">From Pain to Peace,<br>We're Here for You</h2>
</section>
<div class="follow">Follow Us</div>
<div class="follow-line"></div>
<div class="follow-icons"><span></span><span></span><span></span><span></span></div>

<!-- projects -->
<h2 class="projects-title serif">Recent Projects</h2>
<div class="projects-sub">Our Latest Case Studies</div>
<div class="photo" role="img" aria-label="Two women in conversation in an office" style="left:78px;top:2755px;width:137px;height:219px;border-radius:8px;background:linear-gradient(160deg,#d6cfc6,#8f7d6f)"></div>
<div class="photo" role="img" aria-label="Parent and child sitting together on a sofa with a counsellor" style="left:233px;top:2755px;width:334px;height:293px;border-radius:8px;background:linear-gradient(160deg,#cfc6bd,#5e4b40)"></div>
<div class="photo" role="img" aria-label="Smiling psychologist taking notes in a bright room" style="left:588px;top:2843px;width:538px;height:360px;background:linear-gradient(120deg,#e8e6e3,#b4aaa0 50%,#7c6e64)"></div>
<div class="arrow-btn" style="top:3097px"><svg width="10" height="10" viewBox="0 0 10 10"><path d="M3 1l4 4-4 4" stroke="#fff" stroke-width="1.6" fill="none"/></svg></div>
<div class="arrow-btn" style="top:3144px"><svg width="10" height="10" viewBox="0 0 10 10"><path d="M7 1L3 5l4 4" stroke="#fff" stroke-width="1.6" fill="none"/></svg></div>
<div class="proj-card"><h4>Recent Programs</h4><p class="small" style="font-size:10px;line-height:16px">Lorem ipsum dolor sit amet, consectetur adipiscing elit, se d do eiusmod tempor incididunt</p></div>

<!-- reasons -->
<div class="abs" style="left:0;top:3328px;width:965px;height:72px;background:var(--pink-soft)"></div>
<div class="abs" style="left:0;top:3400px;width:467px;height:610px;background:var(--pink-soft)"></div>
<div class="photo" role="img" aria-label="Psychologist with a tablet talking to a client in a modern lounge" style="left:133px;top:3400px;width:1067px;height:536px;background:linear-gradient(110deg,#5a4a40,#a08876 40%,#ded8d2 70%,#f2efec)"></div>
<section class="reasons-card">
  <h2 class="serif">Some Reasons Why You Should Choose Us</h2>
  <p>Lorem ipsum dolor sit amet, consectetur adipiscing elit, se d do eiusmod tempor incididunt ut labore et dolore magn a aliqua. Ut enim ad minim veniam, quis nostrud exercitation ullamco laboris nisi</p>
  <ul class="ticks">
    <li><i></i>Lorem ipsum dolor sit amet, consectetur adipis</li>
    <li><i></i>Lorem ipsum dolor sit amet, consectetur adipis</li>
    <li><i></i>Lorem ipsum dolor sit amet, consectetur adipis</li>
    <li><i></i>Lorem ipsum dolor sit amet, consectetur adipis</li>
    <li><i></i>Lorem ipsum dolor sit amet, consectetur adipis</li>
  </ul>
  <div class="btn btn-orange" style="left:30px;top:364px;width:122px;height:42px">View All</div>
</section>

<!-- contact -->
<h2 class="contact-title serif">Get in touch<br>with us</h2>
<p class="contact-intro">Lorem ipsum dolor sit amet, consectetur adipiscing elit, sed do eiusmod tempor incididunt ut labore et dolore magna aliqua. Ut enim</p>
<div class="contact-rule"></div>
<div class="contact-item" style="top:4382px"><span class="ci"><svg width="12" height="14" viewBox="0 0 12 14"><path d="M6 13s5-5 5-8A5 5 0 0 0 1 5c0 3 5 8 5 8z" fill="#a3308f"/><circle cx="6" cy="5" r="1.8" fill="#fff"/></svg></span>18 Wattle Lane</div>
<div class="contact-item" style="top:4444px"><span class="ci"><svg width="12" height="12" viewBox="0 0 24 24"><path d="M6.6 10.8a15 15 0 0 0 6.6 6.6l2.2-2.2c.3-.3.7-.4 1-.2 1.1.4 2.3.6 3.6.6.6 0 1 .4 1 1V20c0 .6-.4 1-1 1A17 17 0 0 1 3 4c0-.6.4-1 1-1h3.5c.6 0 1 .4 1 1 0 1.3.2 2.5.6 3.6.1.3 0 .7-.2 1z" fill="#a3308f"/></svg></span>+61 2 9014 3372</div>
<div class="contact-item" style="top:4498px"><span class="ci"><svg width="12" height="10" viewBox="0 0 12 10"><rect width="12" height="10" rx="1" fill="#a3308f"/><path d="M0 1l6 4 6-4" stroke="#fff" fill="none"/></svg></span>hello@clarahayes.example</div>

<form class="form-card">
  <label style="left:32px;top:48px">Full Name:</label>
  <div class="field" style="left:30px;top:83px;width:424px;height:44px">Sed non neque elit</div>
  <label style="left:32px;top:150px">Email:</label>
  <div class="field" style="left:30px;top:185px;width:197px;height:44px">Sed non neque elit</div>
  <label style="left:258px;top:150px">Phone-no:</label>
  <div class="field" style="left:257px;top:185px;width:197px;height:44px">Sed non neque elit</div>
  <label style="left:32px;top:258px">Messages:</label>
  <div class="field" style="left:30px;top:294px;width:424px;height:128px">Sed non neque elit</div>
  <div class="btn btn-orange" style="left:30px;top:450px;width:128px;height:42px;border-radius:0">SUBMIT</div>
</form>

<!-- footer -->
<footer class="footer">
  <div class="brand" style="left:86px;top:86px"><span class="brand-dot" style="background:#fff"></span><span class="brand-name" style="color:#fff">DR CLARA HAYES<small style="color:#fff">CLINICAL PSYCHOLOGIST</small></span></div>
  <div class="abs" style="left:84px;top:166px;font-size:18px;font-weight:700">1300-482-915</div>
  <div class="abs" style="left:84px;top:192px;font-size:13px;font-weight:500">Call for free consultation</div>
  <p class="abs" style="left:84px;top:236px;width:270px;font-size:13px;line-height:22px">Lorem ipsum dolor sit amet, consectet sed do eiusmod tempor incididunt ut la magna aliqua. Ut enim</p>
  <div class="abs" style="left:84px;top:316px;font-size:13px;font-weight:700">Read more &nbsp;›</div>

  <h5 style="left:438px;top:84px">Useful Links</h5>
  <ul class="foot-links" style="left:442px;top:154px"><li>About Company</li><li>Leadership</li><li>Blog Post</li><li>FAQ'S</li><li>Certification</li><li>Testimonials</li></ul>
  <ul class="foot-links" style="left:606px;top:154px"><li>Services</li><li>Industries</li><li>Feedback</li><li>Partners</li><li>Pricing</li><li>Contct</li></ul>

  <h5 style="left:789px;top:84px">Newsletter</h5>
  <p class="abs" style="left:786px;top:176px;width:320px;font-size:12px;font-weight:500;line-height:22px">Dont miss to subscribe to our news feeds, kindly fill the form below</p>
  <div class="sub">Your Email Address<span><svg width="14" height="14" viewBox="0 0 10 10"><path d="M3 1l4 4-4 4" stroke="#fff" stroke-width="1.8" fill="none"/></svg></span></div>

  <div class="info-bar">
    <div class="info" style="left:30px"><svg width="26" height="30" viewBox="0 0 12 14"><path d="M6 13s5-5 5-8A5 5 0 0 0 1 5c0 3 5 8 5 8z" fill="none" stroke="#a3308f"/><circle cx="6" cy="5" r="1.8" fill="none" stroke="#a3308f"/></svg><div><b>Location</b><br>42 Harbour St, NSW 2000</div></div>
    <div class="info" style="left:370px"><svg width="30" height="30" viewBox="0 0 20 20"><rect x="2" y="3" width="16" height="12" rx="1" fill="none" stroke="#a3308f" stroke-width="1.3"/><path d="M5 7h10M5 10h7" stroke="#a3308f"/></svg><div><b>Mail us</b><br>care@clarahayes.example</div></div>
    <div class="info" style="left:710px"><svg width="30" height="30" viewBox="0 0 20 20"><path d="M2 9l16-7-6 16-3-7z" fill="none" stroke="#a3308f" stroke-width="1.3"/></svg><div><b>Office hrs</b><br>9.00am to 7.00pm (Mon-Sat)</div></div>
  </div>
</footer>
<div class="legal" style="left:86px">Dr Clara Hayes</div>
<div class="legal" style="left:801px">Privacy Policy &nbsp;&nbsp;&nbsp;&nbsp; Terms &amp; Conditions &nbsp;&nbsp;&nbsp;&nbsp; Site Map</div>
<div class="to-top"><svg width="16" height="16" viewBox="0 0 10 10"><path d="M1 7l4-4 4 4" stroke="#fff" stroke-width="1.6" fill="none"/></svg></div>

</body>
</html>
```